New Business Card Design Project

Need a design that will create an impact / strong impression towards our clients for our business. We are in the lighting business and we do lighting retrofits for large commercial to industrial clientele.

Target Market(s)

Lighting Industry

Industry/Entity Type

Business

Font styles to use
Other font styles liked:
• we would like to use the font on our logo, not sure what it is though..

Requirements
Must have
• Our logo.
Nice to have
• We are open to suggestions that have to do with lighting.

```html
<!DOCTYPE html>
<html lang="en">
<head>
<meta charset="utf-8">
<title>Brightwell Retrofit Group – Business Card</title>
<link href="https://fonts.googleapis.com/css2?family=Lato:wght@400;700;900&display=swap" rel="stylesheet">
<style>
  :root {
    --backdrop: #4a4a4c;
    --card: #ffffff;
    --forest: #10380f;
    --emerald: #0b8a3a;
    --leaf: #6cc24a;
    --ink: #1c1c1c;
    --paper-text: #ffffff;
  }
  * { box-sizing: border-box; margin: 0; padding: 0; }
  html, body {
    width: 1200px; height: 900px; overflow: hidden;
    background: var(--backdrop);
    font-family: "Lato", Arial, sans-serif;
  }
  .canvas { position: relative; width: 1200px; height: 900px; }
  .card {
    position: absolute; left: 250px; width: 700px; height: 400px;
    background: var(--card); overflow: hidden;
    box-shadow: 0 10px 24px rgba(0,0,0,.35);
  }
  .card--front { top: 30px; }
  .card--back { top: 470px; }

  .brand { display: flex; align-items: center; gap: 14px; }
  .brand__square { width: 26px; height: 26px; background: var(--emerald); flex: none; }
  .brand__name {
    font-weight: 900; color: var(--emerald);
    letter-spacing: .5px; line-height: 1;
  }
  .card--front .brand {
    position: absolute; left: 0; right: 0; top: 150px; justify-content: center;
  }
  .card--front .brand__name { font-size: 44px; }
  .front__web {
    position: absolute; left: 0; right: 0; top: 300px; text-align: center;
    font-size: 18px; letter-spacing: 1px; color: var(--ink);
  }

  .back__shapes { position: absolute; inset: 0; }
  .card--back .brand {
    position: absolute; left: 34px; top: 150px;
    align-items: flex-start; gap: 12px;
  }
  .card--back .brand__square { width: 20px; height: 20px; margin-top: 3px; }
  .card--back .brand__name { font-size: 24px; line-height: 1.15; }

  .contact { position: absolute; left: 420px; top: 62px; color: var(--paper-text); }
  .contact__name { font-size: 28px; font-weight: 700; color: var(--emerald); }
  .contact__role { font-size: 19px; margin-top: 2px; }
  .contact__address { font-size: 19px; line-height: 1.3; margin-top: 26px; }
  .contact__list { list-style: none; margin-top: 26px; font-size: 19px; line-height: 1.5; }
  .contact__list li { display: flex; align-items: center; gap: 14px; }
  .contact__icon { width: 16px; height: 16px; flex: none; fill: var(--emerald); }
</style>
</head>
<body>
<div class="canvas">

  <section class="card card--front">
    <div class="brand">
      <span class="brand__square"></span>
      <span class="brand__name">Brightwell Retrofit Group</span>
    </div>
    <p class="front__web">www.brightwell-retrofit.com</p>
  </section>

  <section class="card card--back">
    <svg class="back__shapes" width="700" height="400" viewBox="0 0 700 400">
      <path d="M330 0 C262 120 236 260 244 400 L262 400 C258 260 284 120 352 0 Z" fill="var(--emerald)"/>
      <path d="M372 0 C298 120 266 260 272 400 L700 400 L700 0 Z" fill="var(--forest)"/>
      <path d="M362 0 C290 120 258 260 264 400 L274 400 C268 260 300 120 374 0 Z" fill="var(--emerald)"/>
    </svg>

    <div class="brand">
      <span class="brand__square"></span>
      <span class="brand__name">Brightwell<br>Retrofit Group</span>
    </div>

    <div class="contact">
      <p class="contact__name">Mark Ellison</p>
      <p class="contact__role">Manager</p>
      <p class="contact__address">2148 North Carver Avenue<br>Elmdale, IL 60488</p>
      <ul class="contact__list">
        <li>
          <svg class="contact__icon" viewBox="0 0 16 16"><path d="M3 1l3 3-1.5 2a9 9 0 0 0 5.5 5.5L12 10l3 3-2 2C7 15 1 9 1 3z"/></svg>
          (555) 014-2270
        </li>
        <li>
          <svg class="contact__icon" viewBox="0 0 16 16"><rect x="4" y="1" width="8" height="4"/><rect x="1" y="6" width="14" height="6" rx="1"/><rect x="4" y="10" width="8" height="5"/></svg>
          (555) 014-2271
        </li>
        <li>
          <svg class="contact__icon" viewBox="0 0 16 16"><path d="M1 3h14v10H1z M1 3l7 6 7-6" stroke="var(--forest)" stroke-width="1.2"/></svg>
          info@brightwell-retrofit.com
        </li>
        <li>
          <svg class="contact__icon" viewBox="0 0 16 16"><circle cx="8" cy="8" r="7"/><path d="M1 8h14M8 1c-3 4-3 10 0 14M8 1c3 4 3 10 0 14" stroke="var(--forest)" stroke-width="1" fill="none"/></svg>
          www.brightwell-retrofit.com
        </li>
      </ul>
    </div>
  </section>

</div>
</body>
</html>
```